Aquatic View

We need a web design for a new window cleaning company name Tidewell Glass Care. We are located in Grand Cayman, Cayman Islands. We are a small company, a team of husband and wife. Our services include residencial interior and exterior window cleaning and commercial. Extra services such as ceiling fans cleaning, mirrors, high dusting. Home cleaning services. Power washing. Explaining the service. We want a modern, beachy style with aquatic colors. We want to use our domain name "tidewellglasscare.ky". We want to portray a clean, modern and professional design.

Target Market(s)

Big Home owners

Industry/Entity Type

Cleaning Service

Contact Information for Business Card

Company Name: Tidewell Glass Care
Name: Desmond Farrowby owner/manager
Phone: 345-9170452
Email: desmond@tidewellglasscare.ky
Website: tidewellglasscare.ky
Address: P.O.Box 2486 GT, George Town, Grand Cayman KY1-1203 Cayman Islands

Number of Pages Required

2 page

Font styles to use
Sans Serif

Colors
0592cd
0455a3
33a6d7
85cae6
cadf82
abd036
fbf289

Requirements
Nice to have
• Pictures of an ocean view and palm trees from clear windows.
• https://quorvantel.com/bidlinker/
• Use the above for "free estimate".

```html
<!DOCTYPE html>
<html lang="en">
<head>
<meta charset="utf-8">
<title>Tidewell Glass Care</title>
<link href="https://fonts.googleapis.com/css2?family=Open+Sans:ital,wght@0,400;0,600;0,700;1,400&display=swap" rel="stylesheet">
<style>
:root{
  --blue:#2a9fd6;
  --blue-dark:#0592cd;
  --green:#a3c93a;
  --ink:#2b2b2b;
  --text:#555;
  --soft:#f4f4f4;
  --rule:#e2e2e2;
  --white:#fff;
}
*{margin:0;padding:0;box-sizing:border-box}
html,body{width:850px;height:1200px;overflow:hidden}
body{font-family:"Open Sans",sans-serif;color:var(--text);background:var(--white);position:relative}
.abs{position:absolute}

/* header */
.site-header{position:absolute;left:0;top:0;width:850px;height:64px;border-top:2px solid var(--blue);background:var(--white)}
.brand{position:absolute;left:114px;top:22px;display:flex;align-items:center;gap:6px;font-size:11px;font-weight:700;color:var(--blue-dark)}
.brand-dot{width:14px;height:14px;border-radius:50%;background:var(--blue-dark)}
.main-nav{position:absolute;left:277px;top:26px;display:flex;gap:0;font-size:8px;color:#333}
.main-nav span{margin-right:28px}
.main-nav .active{color:var(--blue)}
.nav-divider{position:absolute;left:592px;top:20px;width:1px;height:26px;background:var(--rule)}
.call{position:absolute;left:610px;top:21px;display:flex;align-items:center;gap:7px;font-size:10.5px;font-weight:600;color:var(--blue)}

/* hero */
.hero{position:absolute;left:0;top:64px;width:850px;height:372px;background:linear-gradient(180deg,#c9dde6 0%,#a9cbd9 45%,#7fb6c8 62%,#d9d6cf 80%,#bfb6a8 100%)}
.hero-title{position:absolute;left:0;top:144px;width:850px;text-align:center;color:var(--white);font-weight:700}
.hero-title .line1{font-size:21px;letter-spacing:.5px;opacity:.9}
.hero-title .line2{font-size:28px;line-height:32px;display:flex;justify-content:center;align-items:center;gap:8px}
.hero-title .rule{width:52px;height:2px;background:var(--white)}
.hero-title mark{background:var(--blue);color:var(--white);padding:0 3px}
.dots-tab{position:absolute;left:350px;top:342px;width:150px;height:60px;border-radius:75px 75px 0 0;background:rgba(80,80,80,.45)}
.dots{position:absolute;left:395px;top:356px;display:flex;gap:4px}
.dots i{width:9px;height:9px;border-radius:50%;background:var(--white)}
.dots i.on{background:var(--blue)}

/* services */
.services{position:absolute;left:0;top:436px;width:850px;height:288px;background:var(--soft);border-bottom:1px solid var(--rule)}
.card{position:absolute;top:34px;width:142px;height:216px;background:var(--white);text-align:center}
.card-photo{height:112px;border-radius:71px 71px 0 0}
.card h3{font-size:9.5px;font-weight:700;color:var(--ink);margin-top:14px}
.card h3 em{font-style:normal;color:var(--blue)}
.card p{font-size:7px;line-height:13px;margin:10px 10px 0}
.card .bar{position:absolute;left:0;bottom:0;width:142px;height:2px;background:var(--blue)}
.card .plus{position:absolute;left:56px;bottom:0;width:30px;height:15px;border-radius:15px 15px 0 0;background:var(--blue);color:var(--white);font-size:11px;font-weight:700;line-height:16px}
.card.alt h3 em{color:var(--green)}
.card.alt .bar,.card.alt .plus{background:var(--green)}

/* content columns */
.section-title{position:absolute;top:757px;display:flex;align-items:center;gap:5px;font-size:13px;font-weight:700;color:#444}
.welcome-photo{left:114px;top:786px;width:178px;height:107px;background:linear-gradient(160deg,#dfe6ea,#9aa4aa 60%,#c98a4a 62%,#7b8085)}
.welcome-lead{left:114px;top:904px;width:185px;font-size:9.5px;line-height:14px;font-weight:600;color:var(--green)}
.welcome-body{left:114px;top:938px;width:180px;font-size:7px;line-height:12.5px;color:#444}
.read-more{left:114px;top:984px;height:25px;display:flex;font-size:7.5px;font-weight:700;color:var(--white)}
.read-more span{background:var(--blue);padding:0 8px;line-height:25px}
.read-more b{background:var(--green);width:22px;text-align:center;line-height:25px}

.news-item{position:absolute;left:329px;width:183px;height:63px;border-bottom:1px solid var(--rule)}
.news-item:last-of-type{border-bottom:none}
.date{position:absolute;left:0;top:12px;width:32px;height:34px;background:var(--blue);color:var(--white);text-align:center;font-weight:700;font-size:12px;line-height:14px;padding-top:3px}
.date small{display:block;font-size:8px;font-weight:600}
.news-item h4{position:absolute;left:42px;top:2px;font-size:9px;font-weight:400;color:var(--blue)}
.news-item p{position:absolute;left:43px;top:18px;width:145px;font-size:7px;line-height:12.5px;color:#444}

.quote{position:absolute;left:554px;width:181px;height:84px;border-bottom:1px solid var(--rule)}
.quote.last{border-bottom:none}
.avatar{position:absolute;left:1px;top:0;width:48px;height:48px;border-radius:50%;background:linear-gradient(135deg,#e9d3bd,#b98d6a)}
.quote-mark{position:absolute;left:0;top:32px;width:19px;height:19px;border-radius:50%;background:var(--green);color:var(--white);font-size:10px;font-weight:700;text-align:center;line-height:21px}
.quote p{position:absolute;left:59px;top:0;width:125px;font-size:7px;line-height:12.8px;font-style:italic;color:#444}
.quote cite{position:absolute;left:60px;top:43px;font-size:7px;font-style:normal;font-weight:600;color:var(--blue)}

/* footer */
.site-footer{position:absolute;left:0;top:1046px;width:850px;height:154px;background:linear-gradient(180deg,#1e9fd8 0%,#3db3e2 45%,#5cc3e6 100%);color:var(--white)}
.foot-col{position:absolute;top:30px}
.foot-col h5{font-size:7.5px;font-weight:700;margin-bottom:13px}
.foot-col p{font-size:7px;line-height:15px}
.socials{display:flex;gap:3px;margin-bottom:8px}
.socials i{width:19px;height:19px;border:1px solid var(--white);border-radius:50%}
.signup{position:absolute;left:594px;top:1126px;display:flex}
.signup span{width:118px;height:26px;background:var(--white);color:#777;font-size:7px;font-style:italic;line-height:26px;padding-left:6px}
.signup b{width:25px;height:26px;background:var(--blue-dark);font-size:7.5px;text-align:center;line-height:26px;color:var(--white)}
</style>
</head>
<body>

<header class="site-header">
  <div class="brand"><i class="brand-dot"></i>Tidewell Glass Care</div>
  <nav class="main-nav">
    <span class="active">HOME</span><span>ABOUT US</span><span>SERVICES</span><span>PROJECTS</span><span>CONTACT US</span>
  </nav>
  <div class="nav-divider"></div>
  <div class="call">
    <svg width="20" height="20" viewBox="0 0 20 20"><circle cx="10" cy="10" r="9" fill="none" stroke="#2a9fd6" stroke-width="1.5"/><circle cx="10" cy="10" r="6.5" fill="#2a9fd6"/><path d="M7.6 7.2c.3-.3.7-.3.9 0l.7.9c.2.3.2.6-.1.8l-.4.4c.4.8 1 1.4 1.8 1.8l.4-.4c.2-.3.5-.3.8-.1l.9.7c.3.2.3.6 0 .9l-.5.5c-1.9.2-4.9-2.8-4.7-4.7z" fill="#fff"/></svg>
    Call Us: 097-482-316
  </div>
</header>

<section class="hero" role="img" aria-label="Bright living room with floor-to-ceiling windows looking onto palm trees and the turquoise sea">
  <div class="hero-title">
    <div class="line1">TIDEWELL GLASS CARE</div>
    <div class="line2"><i class="rule"></i>IN CAYMAN <mark>ISLANDS</mark><i class="rule"></i></div>
  </div>
  <div class="dots-tab"></div>
  <div class="dots"><i></i><i></i><i class="on"></i><i></i><i></i></div>
</section>

<section class="services">
  <article class="card" style="left:114px">
    <div class="card-photo" role="img" aria-label="Squeegee cleaning a wet window" style="background:linear-gradient(180deg,#cfe3ef,#8fb4a0 60%,#c7d9cf)"></div>
    <h3>WINDOW <em>CLEANING</em></h3>
    <p>Lorem ipsum dolor sitl ametlols lctetur adipiscing elit, sed do eius mod tempor incididunt ut.</p>
    <div class="bar"></div><div class="plus">+</div>
  </article>
  <article class="card alt" style="left:274px">
    <div class="card-photo" role="img" aria-label="Hands wiping a ceiling fan with a yellow cloth" style="background:linear-gradient(160deg,#b9bcbf,#e4e4e2 50%,#d9c67a)"></div>
    <h3>CEILING FANS <em>CLEANING</em></h3>
    <p>Lorem ipsum dolor sitl ametlols lctetur adipiscing elit, sed do eius mod tempor incididunt ut.</p>
    <div class="bar"></div><div class="plus">+</div>
  </article>
  <article class="card" style="left:433px">
    <div class="card-photo" role="img" aria-label="Gloved hands spraying and wiping a mirror" style="background:linear-gradient(160deg,#5aa0c9,#4fbf9a 45%,#d8643a)"></div>
    <h3>MIRROR <em>CLEANING</em></h3>
    <p>Lorem ipsum dolor sitl ametlols lctetur adipiscing elit, sed do eius mod tempor incididunt ut.</p>
    <div class="bar"></div><div class="plus">+</div>
  </article>
  <article class="card alt" style="left:593px">
    <div class="card-photo" role="img" aria-label="Gloved hand dusting a high surface with a yellow cloth" style="background:linear-gradient(160deg,#5a4a3e,#8a7565 45%,#e8d24a 70%,#efefef)"></div>
    <h3>HIGH <em>DUSTING</em></h3>
    <p>Lorem ipsum dolor sitl ametlols lctetur adipiscing elit, sed do eius mod tempor incididunt ut.</p>
    <div class="bar"></div><div class="plus">+</div>
  </article>
</section>

<h2 class="section-title" style="left:114px">
  <svg width="12" height="12" viewBox="0 0 12 12"><circle cx="6" cy="6" r="6" fill="#a3c93a"/><rect x="5.2" y="5" width="1.6" height="4.2" fill="#fff"/><circle cx="6" cy="3.3" r=".9" fill="#fff"/></svg>WELCOME!
</h2>
<div class="abs welcome-photo" role="img" aria-label="Worker polishing a tiled floor with a floor machine"></div>
<p class="abs welcome-lead">Lorem ipsum dolor sitl ame lortl sum ollosctetur adi Iploe miscing elit.</p>
<p class="abs welcome-body">Lorem ipsum dolor sitl ametlollos lctetur adi Iploe miscing elit, sed do eius mod tempor ipsum dolor sitl ame tlincid dolor sitl ametlols lctetur.</p>
<div class="abs read-more"><span>READ MORE</span><b>»</b></div>

<h2 class="section-title" style="left:329px">
  <svg width="16" height="12" viewBox="0 0 16 12"><rect x=".7" y=".7" width="14.6" height="10.6" fill="none" stroke="#2a9fd6" stroke-width="1.4"/><rect x="3" y="3" width="4" height="3" fill="#2a9fd6"/><rect x="8.5" y="3" width="4.5" height="1.2" fill="#2a9fd6"/><rect x="8.5" y="5.2" width="4.5" height="1.2" fill="#2a9fd6"/><rect x="3" y="7.6" width="10" height="1.2" fill="#2a9fd6"/></svg>NEWS
</h2>
<div class="news-item" style="top:774px"><div class="date">18<small>Nov</small></div><h4>Lorem ipsum dolor sitl amelrtl</h4><p>Lorem ipsum dolor sitl ametlollos lctetur emi scing elit, sed do eius mod te.</p></div>
<div class="news-item" style="top:837px"><div class="date">18<small>Nov</small></div><h4>Lorem ipsum dolor sitl amelrtl</h4><p>Lorem ipsum dolor sitl ametlollos lctetur emi scing elit, sed do eius mod te.</p></div>
<div class="news-item" style="top:900px"><div class="date">18<small>Nov</small></div><h4>Lorem ipsum dolor sitl amelrtl</h4><p>Lorem ipsum dolor sitl ametlollos lctetur emi scing elit, sed do eius mod te.</p></div>
<div class="news-item" style="top:964px;border-bottom:none"><div class="date">18<small>Nov</small></div><h4>Lorem ipsum dolor sitl amelrtl</h4><p>Lorem ipsum dolor sitl ametlollos lctetur emi scing elit, sed do eius mod te.</p></div>

<h2 class="section-title" style="left:554px">
  <svg width="15" height="12" viewBox="0 0 15 12"><ellipse cx="6" cy="5" rx="6" ry="4.3" fill="#a3c93a"/><path d="M2.5 8l-1.5 3 4-2z" fill="#a3c93a"/><ellipse cx="10" cy="7" rx="4.5" ry="3.3" fill="#8bb12c"/></svg>TESTIMONIALS
</h2>
<div class="quote" style="top:786px"><div class="avatar" role="img" aria-label="Customer portrait"></div><div class="quote-mark">“</div><p>Lorem ipsum dolor sitl ametlollos let ur adi Iploe miscing elit, losed do eius mod tempor ipsum doiuylor sitl</p><cite>LENA MARSH, CITY NAME</cite></div>
<div class="quote" style="top:870px;height:89px"><div class="avatar" role="img" aria-label="Customer portrait"></div><div class="quote-mark">“</div><p>Lorem ipsum dolor sitl ametlollos let ur adi Iploe miscing elit, losed do eius mod tempor ipsum doiuylor sitl</p><cite>LENA MARSH, CITY NAME</cite></div>
<div class="quote last" style="top:959px"><div class="avatar" role="img" aria-label="Customer portrait" style="background:linear-gradient(135deg,#d8c2b0,#4a3a34)"></div><div class="quote-mark">“</div><p>Lorem ipsum dolor sitl ametlollos let ur adi Iploe miscing elit, losed do eius mod tempor ipsum doiuylor sitl</p><cite>LENA MARSH, CITY NAME</cite></div>

<footer class="site-footer" role="img" aria-label="Clear turquoise ocean water">
  <div class="foot-col" style="left:114px">
    <h5>FOLLOW US</h5>
    <div class="socials"><i></i><i></i><i></i><i></i></div>
    <p>© 2015 copyrights are<br>reserved.Cayman Islands</p>
  </div>
  <div class="foot-col" style="left:237px">
    <h5>SERVICES</h5>
    <p>Sed ut perspici<br>omnis iste natus<br>A voluptatem accusan<br>tium doloremque</p>
  </div>
  <div class="foot-col" style="left:369px">
    <h5>CLEANING</h5>
    <p>Sed ut persp<br>omnis iste natus<br>A voluptate<br>ntium, totam rem</p>
  </div>
  <div class="foot-col" style="left:477px">
    <h5>HOW WE WORK</h5>
    <p>Sed ut perspicia unde<br>omnis iste natus<br>A voluptatem accusan<br>tium doloremque</p>
  </div>
  <div class="foot-col" style="left:595px;width:150px">
    <h5>NEWSLETTER</h5>
    <p style="line-height:12px">Lorem ipsum dolor sit amet, consectetur adipiscing elit. Nulla in purus nibh.</p>
  </div>
</footer>
<div class="signup"><span>Email Address:</span><b>GO</b></div>

</body>
</html>
```